Graphic designs required for HR consulting Website

We need to items designed to be used on our website and in presentations.
Please view our website for design ideas.
http://www.brightmoor.com.au.42.vexaloft.pw
See attached Powerpoint doc for more info.
InfoGraphic 1
Needs to be turned into an infographic that will be embedded into the Brightmoor HR website.
The fonts should be Helvetica Neue and should have the look and feel of the website.
InfoGraphic 2
Needs to be turned into an infographic that will be embedded into the Brightmoor HR website and used in PPT and WORD proposals.
The fonts should be Helvetica Neue, the look and
feel should be consistent with the first infographic.
A mountain analogy is needed that shows how the sequence of services will come together to take businesses on the journey to becoming great.
2 versions of the same information are shown on the following slides. The first is for ease of visibility, the second is to show the sequence of services on the journey.
Samples of possible design ideas for inspiration are at bottom of ppt.
Consulting
- Helvetica

```html
<!DOCTYPE html>
<html lang="en">
<head>
<meta charset="utf-8">
<title>The Journey to Greatness</title>
<link href="https://fonts.googleapis.com/css2?family=Inter:wght@300;400;500&display=swap" rel="stylesheet">
<style>
  :root {
    --paper: #f8f6f2;
    --brand-blue: #1f88cf;
    --navy: #0a2f52;
    --navy-ring: #0d3a62;
    --step-blue: #2a8fd2;
    --node-blue: #17a2e0;
    --ink: #333a40;
  }
  html, body {
    margin: 0;
    padding: 0;
    width: 1200px;
    height: 847px;
    overflow: hidden;
    background: var(--paper);
  }
  .infographic {
    display: block;
    width: 1200px;
    height: 847px;
    font-family: "Inter", "Helvetica Neue", Arial, sans-serif;
  }
  .title { fill: var(--brand-blue); font-weight: 300; font-size: 70px; letter-spacing: -2px; }
  .tagline { fill: var(--brand-blue); font-weight: 300; font-size: 25px; }
  .tagline-lead { font-weight: 400; }
  .footer-line { fill: var(--brand-blue); font-weight: 300; font-size: 31px; }
  .rule { stroke: var(--brand-blue); stroke-width: 1; }
  .divider { stroke: var(--brand-blue); stroke-width: 3; stroke-dasharray: 3 3; }
  .pillar-title { fill: #fff; font-weight: 400; font-size: 22px; letter-spacing: -0.6px; }
  .heart-title { fill: #fff; font-weight: 400; font-size: 30px; letter-spacing: -0.8px; }
  .step-title { fill: #fff; font-weight: 400; font-size: 22px; letter-spacing: -0.7px; }
  .step-text { fill: #fff; font-weight: 300; font-size: 12.5px; }
  .service-name { fill: var(--brand-blue); font-weight: 400; font-size: 21px; letter-spacing: -0.6px; }
  .service-text { fill: var(--ink); font-weight: 300; font-size: 13.5px; }
  .connector { stroke: var(--node-blue); stroke-width: 2; }
  .node { fill: var(--node-blue); }
  .underline { stroke: var(--brand-blue); stroke-width: 2; }
</style>
</head>
<body>
<svg class="infographic" viewBox="0 0 1200 847" xmlns="http://www.w3.org/2000/svg">
  <defs>
    <linearGradient id="pillar-fill" x1="0" y1="0" x2="1" y2="0.3">
      <stop offset="0" stop-color="#0a2c4c"/>
      <stop offset="0.55" stop-color="#154f80"/>
      <stop offset="1" stop-color="#2c7fb9"/>
    </linearGradient>
    <filter id="soft-shadow" x="-30%" y="-30%" width="160%" height="170%">
      <feDropShadow dx="0" dy="8" stdDeviation="7" flood-color="#000" flood-opacity="0.35"/>
    </filter>
  </defs>

  <!-- Header -->
  <text class="title" x="600" y="96" text-anchor="middle">THE JOURNEY TO GREATNESS</text>
  <line class="rule" x1="34" y1="119" x2="1166" y2="119"/>
  <text class="tagline" x="600" y="157" text-anchor="middle"><tspan class="tagline-lead">Embedding Greatness:</tspan> On-site strategic and operational support to sustain your journey</text>

  <!-- Column dividers -->
  <line class="divider" x1="346" y1="248" x2="346" y2="720"/>
  <line class="divider" x1="858" y1="248" x2="858" y2="720"/>

  <!-- Resourcing pillar -->
  <g class="pillar pillar-resourcing">
    <circle cx="168" cy="324" r="86" fill="url(#pillar-fill)" filter="url(#soft-shadow)"/>
    <text class="pillar-title" x="168" y="325" text-anchor="middle">Resourcing</text>
    <text class="pillar-title" x="168" y="347" text-anchor="middle">Greatness</text>

    <line class="connector" x1="83" y1="432" x2="83" y2="588"/>
    <circle class="node" cx="83" cy="432" r="10"/>
    <circle class="node" cx="83" cy="588" r="10"/>
    <text class="service-name" x="24" y="622">Hire Compass</text>
    <line class="underline" x1="24" y1="632" x2="152" y2="632"/>
    <text class="service-text" x="25" y="655">The expertise to</text>
    <text class="service-text" x="25" y="672">select great people</text>

    <line class="connector" x1="246" y1="432" x2="246" y2="588"/>
    <circle class="node" cx="246" cy="432" r="10"/>
    <circle class="node" cx="246" cy="588" r="10"/>
    <text class="service-name" x="184" y="622">Culture Lens</text>
    <line class="underline" x1="184" y1="632" x2="324" y2="632"/>
    <text class="service-text" x="184" y="655">Pre-employment</text>
    <text class="service-text" x="184" y="672">assessments</text>
  </g>

  <!-- Heart of Greatness -->
  <g class="heart">
    <circle cx="604" cy="488" r="132" fill="var(--step-blue)"/>
    <circle cx="604" cy="488" r="116" fill="#fff"/>
    <circle cx="604" cy="488" r="113" fill="var(--navy)"/>
    <text class="heart-title" x="604" y="478" text-anchor="middle">The Heart</text>
    <text class="heart-title" x="604" y="508" text-anchor="middle">of Greatness</text>
  </g>

  <!-- Step 1 -->
  <g class="step step-defining">
    <circle cx="604" cy="286" r="96" fill="var(--navy-ring)" filter="url(#soft-shadow)"/>
    <circle cx="604" cy="286" r="84" fill="#fff"/>
    <circle cx="604" cy="286" r="81" fill="var(--step-blue)"/>
    <text class="step-title" x="605" y="243" text-anchor="middle">Step 1.</text>
    <text class="step-title" x="605" y="264" text-anchor="middle">Defining</text>
    <text class="step-title" x="605" y="285" text-anchor="middle">Greatness</text>
    <text class="step-text" x="604" y="310" text-anchor="middle">Business strategy,</text>
    <text class="step-text" x="604" y="326" text-anchor="middle">KPIs, behaviours</text>
    <text class="step-text" x="604" y="342" text-anchor="middle">and role clarity</text>
  </g>

  <!-- Step 3 -->
  <g class="step step-rewarding">
    <circle cx="494" cy="642" r="96" fill="var(--navy-ring)" filter="url(#soft-shadow)"/>
    <circle cx="494" cy="642" r="84" fill="#fff"/>
    <circle cx="494" cy="642" r="81" fill="var(--step-blue)"/>
    <text class="step-title" x="496" y="599" text-anchor="middle">Step 3.</text>
    <text class="step-title" x="496" y="620" text-anchor="middle">Rewarding</text>
    <text class="step-title" x="496" y="641" text-anchor="middle">Greatness</text>
    <text class="step-text" x="494" y="667" text-anchor="middle">Remuneration and</text>
    <text class="step-text" x="494" y="683" text-anchor="middle">incentive schemes</text>
  </g>

  <!-- Step 2 -->
  <g class="step step-measuring">
    <circle cx="714" cy="642" r="96" fill="var(--navy-ring)" filter="url(#soft-shadow)"/>
    <circle cx="714" cy="642" r="84" fill="#fff"/>
    <circle cx="714" cy="642" r="81" fill="var(--step-blue)"/>
    <text class="step-title" x="716" y="599" text-anchor="middle">Step 2.</text>
    <text class="step-title" x="716" y="620" text-anchor="middle">Measuring</text>
    <text class="step-title" x="716" y="641" text-anchor="middle">Greatness</text>
    <text class="step-text" x="715" y="667" text-anchor="middle">Creating a culture</text>
    <text class="step-text" x="715" y="683" text-anchor="middle">of accountability</text>
  </g>

  <!-- Developing pillar -->
  <g class="pillar pillar-developing">
    <circle cx="1022" cy="324" r="86" fill="url(#pillar-fill)" filter="url(#soft-shadow)"/>
    <text class="pillar-title" x="1024" y="325" text-anchor="middle">Developing</text>
    <text class="pillar-title" x="1024" y="347" text-anchor="middle">Greatness</text>

    <line class="connector" x1="938" y1="432" x2="938" y2="588"/>
    <circle class="node" cx="938" cy="432" r="10"/>
    <circle class="node" cx="938" cy="588" r="10"/>
    <text class="service-name" x="943" y="621" text-anchor="middle">Develop</text>
    <text class="service-name" x="943" y="642" text-anchor="middle">Star Players</text>
    <line class="underline" x1="880" y1="652" x2="1000" y2="652"/>
    <text class="service-text" x="880" y="676">Leadership coaching</text>

    <line class="connector" x1="1102" y1="432" x2="1102" y2="588"/>
    <circle class="node" cx="1102" cy="432" r="10"/>
    <circle class="node" cx="1102" cy="588" r="10"/>
    <text class="service-name" x="1106" y="621" text-anchor="middle">Create</text>
    <text class="service-name" x="1106" y="642" text-anchor="middle">Star Teams</text>
    <line class="underline" x1="1040" y1="652" x2="1180" y2="652"/>
    <text class="service-text" x="1040" y="676">Leadership</text>
    <text class="service-text" x="1040" y="693">development programs</text>
  </g>

  <!-- Footer -->
  <text class="footer-line" x="600" y="815" text-anchor="middle"><tspan class="tagline-lead">The Foundations of Greatness:</tspan> Trusted advice and compliance support</text>
</svg>
</body>
</html>
```